New Business card design to reflect rebrand

I would like a business card design with a good base colour for our new logo and also a placeholder for a profile pic of the card holder. the design needs to be editable to the point that we can easily change the picture of the person and use that design for printmerlo etc. we are looking at a metalic finish business card so will need a good base colour to bring out the finish.

Target Market(s)

prospective customers

Industry/Entity Type

Business

Contact Information for Business Card

I would like one editable design that we can change the name of the card holder and profile picture. The design need to be in a format that be send to printmerlo etc.

Our address is Fenwick Lodge, Copse Lane, Ashcombe Vale, GU14 3TP Tel no. 01483 556172

Requirements
Must have
• place holder for a profile pic for the card holder. in AI or preferably PSD format

```html
<!DOCTYPE html>
<html lang="en">
<head>
<meta charset="utf-8">
<title>Corvane Workplace Services – Business Card</title>
<link href="https://fonts.googleapis.com/css2?family=Open+Sans:wght@400;600;700&display=swap" rel="stylesheet">
<style>
  :root {
    --orange: #ee6300;
    --navy: #3c4f6b;
    --white: #ffffff;
    --stage: #eceae6;
    --photo-light: #c9ccd3;
    --photo-dark: #272c3f;
  }
  * { margin: 0; padding: 0; box-sizing: border-box; }
  html, body {
    width: 1200px; height: 900px; overflow: hidden;
    background: var(--stage);
    font-family: "Open Sans", Arial, sans-serif;
  }
  .stage {
    width: 1200px; height: 900px;
    display: flex; flex-direction: column;
    align-items: center; justify-content: center; gap: 40px;
  }
  .card {
    position: relative;
    width: 700px; height: 400px;
    overflow: hidden;
    box-shadow: 0 6px 18px rgba(0,0,0,0.18);
  }
  .card-front { background: var(--orange); display: flex; align-items: center; justify-content: center; }
  .brand-name {
    color: var(--navy);
    font-weight: 700;
    text-transform: uppercase;
    line-height: 1.15;
  }
  .card-front .brand-name { font-size: 44px; letter-spacing: 3px; text-align: center; }
  .card-front .brand-name span { display: block; font-size: 26px; letter-spacing: 5px; }

  .card-back { background: var(--white); }
  .card-back .backdrop { position: absolute; inset: 0; }
  .card-back .brand-name {
    position: absolute; left: 80px; top: 62px;
    font-size: 40px; letter-spacing: 3px; text-align: left;
  }
  .card-back .brand-name span { display: block; font-size: 22px; letter-spacing: 4px; }
  .profile-photo {
    position: absolute; left: 468px; top: 22px; width: 232px; height: 378px;
  }
  .holder {
    position: absolute; left: 100px; top: 236px; color: var(--white);
  }
  .holder-name { font-size: 24px; font-weight: 700; line-height: 1.3; margin-bottom: 6px; }
  .contact-line { display: flex; align-items: center; gap: 10px; font-size: 17px; line-height: 1.4; margin-bottom: 3px; }
  .contact-line svg { width: 14px; height: 14px; fill: var(--white); }
  .address { font-size: 17px; line-height: 1.4; margin-top: 10px; padding-left: 24px; }
</style>
</head>
<body>
<main class="stage">
  <section class="card card-front">
    <div class="brand-name">Corvane<span>Workplace Services</span></div>
  </section>

  <section class="card card-back">
    <svg class="backdrop" viewBox="0 0 700 400" preserveAspectRatio="none">
      <polygon points="0,250 700,130 700,400 0,400" fill="var(--orange)"/>
      <line x1="0" y1="244" x2="700" y2="124" stroke="var(--navy)" stroke-width="6"/>
    </svg>
    <svg class="profile-photo" role="img" aria-label="Profile photo of the card holder" viewBox="0 0 232 378" preserveAspectRatio="none">
      <defs>
        <linearGradient id="photoTone" x1="0" y1="0" x2="0" y2="1">
          <stop offset="0" stop-color="var(--photo-light)"/>
          <stop offset="1" stop-color="var(--photo-dark)"/>
        </linearGradient>
      </defs>
      <rect width="232" height="378" fill="url(#photoTone)"/>
    </svg>
    <div class="brand-name">Corvane<span>Workplace Services</span></div>
    <div class="holder">
      <p class="holder-name">Daniel Reeve</p>
      <p class="contact-line">
        <svg viewBox="0 0 24 24"><path d="M6.6 10.8a15.1 15.1 0 0 0 6.6 6.6l2.2-2.2a1 1 0 0 1 1-.25 11.4 11.4 0 0 0 3.6.57 1 1 0 0 1 1 1V20a1 1 0 0 1-1 1A17 17 0 0 1 3 4a1 1 0 0 1 1-1h3.5a1 1 0 0 1 1 1c0 1.25.2 2.45.57 3.57a1 1 0 0 1-.25 1z"/></svg>
        01483 556172
      </p>
      <p class="contact-line">
        <svg viewBox="0 0 24 24"><path d="M2 5h20v14H2z M2 5l10 8 10-8" fill="var(--white)" stroke="var(--orange)" stroke-width="1.6"/></svg>
        info@corvane.com
      </p>
      <p class="address">Fenwick Lodge, Copse Lane,<br>Ashcombe Vale, GU14 3TP</p>
    </div>
  </section>
</main>
</body>
</html>
```